Valmora Company needs a Business Card Design

We just opened our business recently and we need a business card design. Our basic product are clothes and accessories. We would like to see designs that use bright colors like pink, light blue and purple. In addition to that kindly include also our address in the business card which our main office is located in Los Angeles, California.
The final design should communicate that we have affordable price yet high quality brand.

Target Market(s)

young and middle age women

Industry/Entity Type

Business

Contact Information for Business Card

Valmora Apparel and Accessories 4873 North Bellcrest St. Los Angeles California
Tel: 555-318-6492

Logo Text

Valmora's Apparel and Accessories

Font styles to use
Serif

Requirements
Must have
• there should be a graphic of a sexy lady wearing an elegant dress at the upper left corner of the business card.

```html
<!DOCTYPE html>
<html lang="en">
<head>
<meta charset="utf-8">
<title>Valmora Apparel and Accessories – Business Card</title>
<link href="https://fonts.googleapis.com/css2?family=Libre+Baskerville:wght@400;700&family=Tinos&display=swap" rel="stylesheet">
<style>
  :root {
    --stage: #e9e6e3;
    --card-white: #f7f7f7;
    --card-white-edge: #e4e4e4;
    --blush-light: #f6d4d8;
    --blush: #eeb3ba;
    --blush-deep: #e29da6;
    --ink: #1e1e1e;
    --ink-soft: #2d2d2d;
    --figure-dark: #2a2a2a;
    --figure-pink: #ec9aa4;
  }
  * { margin: 0; padding: 0; box-sizing: border-box; }
  html, body {
    width: 1200px;
    height: 885px;
    overflow: hidden;
    background: var(--stage);
  }
  .canvas {
    width: 1200px;
    height: 885px;
    display: flex;
    align-items: center;
    justify-content: center;
  }
  .business-card {
    position: relative;
    width: 460px;
    height: 800px;
    border-radius: 30px;
    overflow: hidden;
    box-shadow: 0 10px 30px rgba(0,0,0,0.18);
    display: flex;
    flex-direction: column;
  }
  .card-top {
    height: 44%;
    background: linear-gradient(180deg, var(--card-white) 0%, var(--card-white-edge) 100%);
    display: flex;
    align-items: flex-end;
    justify-content: center;
  }
  .figure-art {
    width: 230px;
    height: 270px;
    margin-bottom: -40px;
    margin-left: 90px;
    border-radius: 40% 40% 12px 12px;
    background: radial-gradient(ellipse at 50% 55%, var(--figure-pink) 0%, var(--figure-dark) 38%, var(--figure-dark) 100%);
    position: relative;
    z-index: 1;
  }
  .card-bottom {
    flex: 1;
    background: linear-gradient(160deg, var(--blush-deep) 0%, var(--blush) 35%, var(--blush-light) 80%, var(--blush) 100%);
    padding: 70px 40px 0 40px;
    display: flex;
    flex-direction: column;
    align-items: center;
  }
  .wordmark {
    text-align: center;
    color: var(--ink);
    font-family: "Libre Baskerville", Georgia, serif;
    font-weight: 700;
  }
  .wordmark-name {
    font-size: 30px;
    letter-spacing: 0.9em;
    margin-right: -0.9em;
    line-height: 1.1;
  }
  .wordmark-tagline {
    font-size: 25px;
    margin-top: 6px;
  }
  .contact {
    margin-top: 100px;
    text-align: center;
    font-family: "Tinos", "Times New Roman", serif;
    color: var(--ink-soft);
  }
  .contact-phone {
    font-size: 22px;
  }
  .contact-address {
    font-size: 19px;
    margin-top: 10px;
  }
</style>
</head>
<body>
<main class="canvas">
  <article class="business-card">
    <section class="card-top">
      <div class="figure-art" role="img" aria-label="Illustration of a kneeling woman in a pink bikini, shown as a dark silhouette"></div>
    </section>
    <section class="card-bottom">
      <div class="wordmark">
        <p class="wordmark-name">Valmora</p>
        <p class="wordmark-tagline">Apparel and Accessories</p>
      </div>
      <div class="contact">
        <p class="contact-phone">555-318-6492</p>
        <p class="contact-address">4873 North Bellcrest St. Los Angeles California</p>
      </div>
    </section>
  </article>
</main>
</body>
</html>
```